Salon Signage

We need a new company sign designed for the exterior of our salon. I have attached our current logos for an idea. I have also attached a photo of what salon looks like currently.

```html
<!DOCTYPE html>
<html lang="en">
<head>
<meta charset="utf-8">
<title>Lustrella Beauty Salon – Exterior Signage</title>
<link rel="stylesheet" href="https://fonts.googleapis.com/css2?family=Poppins:ital,wght@0,500;0,600;1,700&family=Montserrat:wght@500;800;900&family=Oswald:wght@200;600&family=Great+Vibes&display=swap">
<style>
  :root {
    --plum: #9c2b90;
    --plum-deep: #7a1d70;
    --charcoal: #2a2526;
    --frame-line: #8e8a8b;
    --wine-dark: #2b0a0e;
    --wine: #6e1c24;
    --wine-light: #a3363e;
    --white: #ffffff;
    --page: #ffffff;
    --badge-blue: #1f6fc0;
  }
  * { margin: 0; padding: 0; box-sizing: border-box; }
  html, body { width: 1200px; height: 3058px; overflow: hidden; background: var(--page); }
  .canvas { position: relative; width: 1200px; height: 3058px; }

  .shadowed { box-shadow: 0 6px 10px rgba(0,0,0,.35); }

  /* ---------- fascia sign ---------- */
  .fascia {
    position: absolute; left: 102px; top: 836px; width: 997px; height: 303px;
    background: var(--charcoal); overflow: hidden;
  }
  .fascia svg.shape { position: absolute; inset: 0; }
  .fascia-tagline {
    position: absolute; left: 36px; top: 50px;
    font-family: "Poppins", sans-serif; font-weight: 700; font-style: italic;
    font-size: 52px; line-height: 56px; color: var(--white);
  }
  .fascia-mark {
    position: absolute; left: 360px; top: 82px; width: 130px; height: 130px;
    border: 6px solid var(--white); border-radius: 50%;
  }
  .fascia-name {
    position: absolute; left: 488px; top: 50px; width: 440px; text-align: center;
    font-family: "Montserrat", sans-serif; font-weight: 900; font-size: 74px;
    letter-spacing: -1px; color: var(--white);
  }
  .fascia-sub {
    position: absolute; left: 640px; top: 122px;
    font-family: "Great Vibes", cursive; font-size: 66px; color: var(--white);
  }
  .fascia-phone {
    position: absolute; left: 654px; top: 218px; width: 300px; height: 54px;
    background: var(--plum); border-radius: 4px 0 0 0;
    display: flex; align-items: center; justify-content: center; gap: 20px;
    font-family: "Montserrat", sans-serif; font-weight: 800; font-size: 36px;
    letter-spacing: 3px; color: var(--white);
  }

  /* ---------- window panels ---------- */
  .panel {
    position: absolute; top: 1280px; width: 469px; height: 941px; overflow: hidden;
  }
  .panel-left { left: 102px; }
  .panel-right { left: 629px; background: var(--wine-dark); }
  .panel svg.shape { position: absolute; inset: 0; }

  .photo-area { position: absolute; }
  .photo-circle { position: absolute; border-radius: 50%; border: 5px solid var(--white); }

  .panel-title {
    position: absolute; left: 52px; top: 34px; color: var(--white);
    font-family: "Oswald", sans-serif; text-transform: uppercase;
  }
  .panel-title .light { display: block; font-weight: 200; font-size: 118px; line-height: 118px; }
  .panel-title .bold { display: block; font-weight: 600; font-size: 88px; line-height: 92px; letter-spacing: -1px; }

  .badge {
    position: absolute; left: 356px; top: 38px; width: 82px; height: 82px;
    background: var(--badge-blue); border: 4px solid var(--white); border-radius: 50%;
  }

  .service-list { position: absolute; list-style: none; color: var(--white); font-family: "Poppins", sans-serif; font-weight: 500; }
  .service-list li { display: flex; align-items: center; gap: 14px; text-transform: uppercase; }
  .service-list svg { flex: none; }
  .list-left { left: 46px; top: 445px; font-size: 28px; }
  .list-left li { height: 52.5px; }
  .list-right { left: 34px; top: 30px; font-size: 33px; letter-spacing: 1px; }
  .list-right li { height: 55px; }

  .panel-phone {
    position: absolute; display: flex; align-items: center; gap: 8px; color: var(--white);
    font-family: "Montserrat", sans-serif; font-weight: 500;
  }
  .panel-left .panel-phone { left: 40px; top: 876px; font-size: 36px; }
  .panel-right .panel-phone { left: 94px; top: 865px; font-size: 46px; letter-spacing: 3px; }

  .corner-mark {
    position: absolute; left: 378px; top: 52px; width: 54px; height: 54px;
    border: 4px solid var(--white); border-radius: 50%;
  }
</style>
</head>
<body>
<main class="canvas">

  <!-- Fascia sign -->
  <section class="fascia shadowed">
    <svg class="shape" width="997" height="303" viewBox="0 0 997 303">
      <path d="M0 0 H335 C 310 130 220 250 80 303 H0 Z" fill="var(--plum)"/>
      <path d="M335 0 C 310 130 220 250 80 303" fill="none" stroke="var(--white)" stroke-width="6"/>
      <path d="M338 30 H945 Q955 30 955 40 V262 Q955 271 945 271 H200" fill="none" stroke="var(--frame-line)" stroke-width="1.5"/>
      <path d="M34 214 C 90 180 200 178 208 210 C 150 196 90 204 34 214 Z" fill="var(--white)"/>
    </svg>
    <div class="fascia-tagline">Hair &amp;<br>Beauty</div>
    <div class="fascia-mark"></div>
    <div class="fascia-name">LUSTRELLA</div>
    <div class="fascia-sub">Beauty Salon</div>
    <div class="fascia-phone">
      <svg width="28" height="28" viewBox="0 0 24 24"><path d="M6.6 10.8a15.1 15.1 0 0 0 6.6 6.6l2.2-2.2c.3-.3.7-.4 1-.2 1.1.4 2.3.6 3.6.6.6 0 1 .4 1 1V20c0 .6-.4 1-1 1C10.6 21 3 13.4 3 4c0-.6.4-1 1-1h3.5c.6 0 1 .4 1 1 0 1.3.2 2.5.6 3.6.1.3 0 .7-.2 1z" fill="var(--white)"/></svg>
      95551234
    </div>
  </section>

  <!-- Left window panel -->
  <section class="panel panel-left shadowed">
    <div class="photo-area" role="img" aria-label="Photo of a red-haired woman with bold makeup and manicured nails" style="inset:0;background:linear-gradient(160deg,var(--wine-light),var(--wine) 45%,var(--wine-dark));"></div>
    <svg class="shape" width="469" height="941" viewBox="0 0 469 941">
      <path d="M0 0 H469 V100 C 420 250 300 350 0 350 Z" fill="var(--plum)"/>
      <path d="M0 350 C 300 350 420 250 469 100 V125 C 420 280 300 380 0 385 Z" fill="var(--white)"/>
      <path d="M0 385 C 300 380 420 280 469 125 V140 C 420 295 300 390 0 400 Z" fill="var(--plum-deep)"/>
      <path d="M0 790 C 90 780 200 790 300 820 C 380 845 440 890 469 941 H0 Z" fill="var(--white)"/>
      <path d="M0 812 C 90 802 200 812 300 842 C 380 867 430 905 450 941 H0 Z" fill="var(--plum)"/>
    </svg>
    <div class="panel-title"><span class="light">Hair</span><span class="bold">Dressing</span></div>
    <div class="badge"></div>
    <ul class="service-list list-left">
      <li><svg width="28" height="24" viewBox="0 0 28 24"><path d="M2 13 L10 21 L26 3" fill="none" stroke="var(--white)" stroke-width="2.5"/></svg>Threading</li>
      <li><svg width="28" height="24" viewBox="0 0 28 24"><path d="M2 13 L10 21 L26 3" fill="none" stroke="var(--white)" stroke-width="2.5"/></svg>Tinting</li>
      <li><svg width="28" height="24" viewBox="0 0 28 24"><path d="M2 13 L10 21 L26 3" fill="none" stroke="var(--white)" stroke-width="2.5"/></svg>Makeup</li>
      <li><svg width="28" height="24" viewBox="0 0 28 24"><path d="M2 13 L10 21 L26 3" fill="none" stroke="var(--white)" stroke-width="2.5"/></svg>Hair Style</li>
      <li><svg width="28" height="24" viewBox="0 0 28 24"><path d="M2 13 L10 21 L26 3" fill="none" stroke="var(--white)" stroke-width="2.5"/></svg>Eyebrow Feathering</li>
      <li><svg width="28" height="24" viewBox="0 0 28 24"><path d="M2 13 L10 21 L26 3" fill="none" stroke="var(--white)" stroke-width="2.5"/></svg>Eyelash Extension</li>
    </ul>
    <div class="photo-circle" role="img" aria-label="Close-up photo of a woman with long lashes and red lips" style="left:262px;top:750px;width:180px;height:180px;background:radial-gradient(circle at 45% 40%,#e9c3b0,#b77c6a 60%,#5a2a26);"></div>
    <div class="panel-phone">
      <svg width="30" height="30" viewBox="0 0 24 24"><path d="M6.6 10.8a15.1 15.1 0 0 0 6.6 6.6l2.2-2.2c.3-.3.7-.4 1-.2 1.1.4 2.3.6 3.6.6.6 0 1 .4 1 1V20c0 .6-.4 1-1 1C10.6 21 3 13.4 3 4c0-.6.4-1 1-1h3.5c.6 0 1 .4 1 1 0 1.3.2 2.5.6 3.6.1.3 0 .7-.2 1z" fill="none" stroke="var(--white)" stroke-width="1.8"/></svg>
      95551234
    </div>
  </section>

  <!-- Right window panel -->
  <section class="panel panel-right shadowed">
    <div class="photo-area" role="img" aria-label="Photo of a woman in profile with auburn hair and dramatic eye makeup" style="left:160px;top:0;right:0;height:520px;background:linear-gradient(100deg,var(--wine-dark),var(--wine) 45%,#9a4a3e 80%,var(--wine));"></div>
    <svg class="shape" width="469" height="941" viewBox="0 0 469 941">
      <path d="M0 560 C 150 600 300 640 469 670 V870 C 300 800 150 830 0 880 Z" fill="var(--plum)"/>
      <path d="M0 870 C 150 800 300 780 469 860 V875 C 300 810 150 835 0 893 Z" fill="var(--white)"/>
    </svg>
    <div class="photo-area" role="img" aria-label="Photo of a young woman with pastel hair rollers and colourful makeup" style="left:0;top:420px;width:250px;height:420px;background:linear-gradient(160deg,#c9a78c,#e7c7b4 45%,#8fb9c9 70%,#7a5b6a);border-radius:0 0 60% 0;"></div>
    <div class="photo-circle" role="img" aria-label="Close-up photo of an eye with glitter lash makeup" style="left:172px;top:430px;width:140px;height:140px;background:radial-gradient(circle,#f1c9c0,#c8808a 60%,#7b3a4a);"></div>
    <div class="photo-circle" role="img" aria-label="Photo of a woman with long straight hair" style="left:292px;top:520px;width:150px;height:150px;background:radial-gradient(circle at 55% 40%,#e3cfb3,#a9855f 60%,#5e4a36);"></div>
    <div class="corner-mark"></div>
    <ul class="service-list list-right">
      <li><svg width="32" height="28" viewBox="0 0 28 24"><path d="M2 13 L10 21 L26 3" fill="none" stroke="var(--white)" stroke-width="2.5"/></svg>Cut</li>
      <li><svg width="32" height="28" viewBox="0 0 28 24"><path d="M2 13 L10 21 L26 3" fill="none" stroke="var(--white)" stroke-width="2.5"/></svg>Colour</li>
      <li><svg width="32" height="28" viewBox="0 0 28 24"><path d="M2 13 L10 21 L26 3" fill="none" stroke="var(--white)" stroke-width="2.5"/></svg>Foils</li>
      <li><svg width="32" height="28" viewBox="0 0 28 24"><path d="M2 13 L10 21 L26 3" fill="none" stroke="var(--white)" stroke-width="2.5"/></svg>Blow Wave</li>
      <li><svg width="32" height="28" viewBox="0 0 28 24"><path d="M2 13 L10 21 L26 3" fill="none" stroke="var(--white)" stroke-width="2.5"/></svg>Treatment</li>
      <li><svg width="32" height="28" viewBox="0 0 28 24"><path d="M2 13 L10 21 L26 3" fill="none" stroke="var(--white)" stroke-width="2.5"/></svg>Straight</li>
      <li><svg width="32" height="28" viewBox="0 0 28 24"><path d="M2 13 L10 21 L26 3" fill="none" stroke="var(--white)" stroke-width="2.5"/></svg>Perms</li>
    </ul>
    <div class="panel-phone">
      <svg width="38" height="38" viewBox="0 0 24 24"><path d="M6.6 10.8a15.1 15.1 0 0 0 6.6 6.6l2.2-2.2c.3-.3.7-.4 1-.2 1.1.4 2.3.6 3.6.6.6 0 1 .4 1 1V20c0 .6-.4 1-1 1C10.6 21 3 13.4 3 4c0-.6.4-1 1-1h3.5c.6 0 1 .4 1 1 0 1.3.2 2.5.6 3.6.1.3 0 .7-.2 1z" fill="none" stroke="var(--white)" stroke-width="1.8"/></svg>
      95551234
    </div>
  </section>

</main>
</body>
</html>
```